Website for Dental Office - The Bright Arch Clinic

The bright arch clinic is a dental office offering cosmetic dentistry, general dentistry, and multi-specialty dental care all under one roof in our state-of-the-art cosmetic dental center. We are particularly striving to provide services that fit the need of the young generation. Thus, we hope to have a modern, professional concise website that represents our spirit.

*Should be able to switch from English to Chinese

6 sections besides homepage:
Home, Meet us, Services,
Patient Info, Cases&Reviews, Blog, Contact

The Services sections should contain multiple subsections such as cleaning and prevention, cosmetic dentistry, implant dentistry, removable dentures, etc...
The Patient Info section is also intended to contain several subsections such as
New Patient offer, accepted Insurance, patient portal, helpful tips, etc...

Target Market(s)

young generation

Coding

Coded - Design and coding required

Number of Pages Required

5+ page

Font styles to use
Sans Serif

Colors
0592cd
33a6d7
85cae6
00a990
33b8a4
86cfc6
cee9f5
cfeae6
3277b5

Requirements
Must have
• *Should be able to switch from English to Chinese
Nice to have
• http://www.thebrightarchclinic.com/
• As a reference, the above link is the current website, but we would like to change the appearance and the content (our new logo's picture is attached)

```html
<!DOCTYPE html>
<html lang="en">
<head>
<meta charset="utf-8">
<title>The Bright Arch Clinic</title>
<link rel="stylesheet" href="https://fonts.googleapis.com/css2?family=Montserrat:wght@600;700;800;900&display=swap">
<style>
  :root {
    --blue-deep: #3277b5;
    --blue: #0592cd;
    --blue-mid: #33a6d7;
    --blue-soft: #85cae6;
    --blue-pale: #cee9f5;
    --green: #00a990;
    --green-mid: #33b8a4;
    --warm-soft: #e6d3c6;
    --warm: #cfae98;
    --ink: #111111;
    --white: #ffffff;
  }
  * { box-sizing: border-box; margin: 0; padding: 0; }
  html, body {
    width: 822px;
    height: 1200px;
    overflow: hidden;
    background: var(--white);
    font-family: "Montserrat", Arial, sans-serif;
  }
  .page {
    position: relative;
    width: 822px;
    height: 1200px;
    overflow: hidden;
    background: var(--white);
  }
  .site-header {
    position: absolute;
    top: 0; left: 0; right: 0;
    height: 140px;
    display: flex;
    align-items: center;
    justify-content: space-between;
    padding: 0 40px;
    border-bottom: 2px solid #eef4f7;
  }
  .brand {
    display: flex;
    align-items: center;
    gap: 20px;
  }
  .brand-mark {
    width: 76px;
    height: 76px;
    background: var(--blue-mid);
  }
  .brand-name {
    color: var(--blue-deep);
    font-weight: 700;
    font-size: 32px;
    line-height: 1.05;
    text-transform: uppercase;
    letter-spacing: 0.5px;
  }
  .header-actions {
    display: flex;
    gap: 16px;
    align-items: center;
  }
  .menu-button {
    width: 80px;
    height: 80px;
    border-radius: 8px;
    background: var(--blue-mid);
    display: flex;
    align-items: center;
    justify-content: center;
  }
  .lang-switch {
    height: 80px;
    padding: 0 20px;
    border-radius: 8px;
    background: var(--green);
    color: var(--white);
    display: flex;
    align-items: center;
    gap: 10px;
    font-size: 28px;
    font-weight: 700;
  }
  .hero-photo {
    position: absolute;
    top: 250px;
    left: 120px;
    width: 670px;
    height: 670px;
    border-radius: 50%;
    overflow: hidden;
    background: linear-gradient(200deg, var(--blue-pale) 0%, var(--blue-pale) 30%, var(--warm-soft) 62%, var(--warm) 100%);
  }
  .call-badge {
    position: absolute;
    top: 190px;
    left: 60px;
    width: 250px;
    height: 250px;
    border-radius: 50%;
    background: var(--blue-deep);
    color: var(--white);
    display: flex;
    flex-direction: column;
    align-items: center;
    justify-content: center;
    gap: 18px;
    font-weight: 700;
    font-size: 28px;
    letter-spacing: 0.5px;
  }
  .hero-title {
    position: absolute;
    left: 0; right: 0;
    top: 955px;
    text-align: center;
    color: var(--ink);
    font-weight: 800;
    font-size: 76px;
    line-height: 1.12;
    text-transform: uppercase;
  }
</style>
</head>
<body>
<div class="page">
  <header class="site-header">
    <div class="brand">
      <div class="brand-mark"></div>
      <div class="brand-name">The Bright<br>Arch Clinic</div>
    </div>
    <div class="header-actions">
      <div class="menu-button" aria-label="Menu">
        <svg width="40" height="32" viewBox="0 0 40 32">
          <rect x="0" y="0" width="40" height="5" rx="2" fill="#ffffff"/>
          <rect x="0" y="13.5" width="40" height="5" rx="2" fill="#ffffff"/>
          <rect x="0" y="27" width="40" height="5" rx="2" fill="#ffffff"/>
        </svg>
      </div>
      <div class="lang-switch">
        <span>中文</span>
        <svg width="20" height="14" viewBox="0 0 20 14">
          <path d="M2 3 L10 11 L18 3" fill="none" stroke="#ffffff" stroke-width="3.5" stroke-linecap="round" stroke-linejoin="round"/>
        </svg>
      </div>
    </div>
  </header>

  <div class="hero-photo" role="img" aria-label="Photo of a smiling young woman pointing at her bright smile"></div>

  <div class="call-badge">
    <svg width="56" height="56" viewBox="0 0 24 24">
      <path fill="#ffffff" d="M6.6 10.8c1.4 2.8 3.8 5.1 6.6 6.6l2.2-2.2c.3-.3.7-.4 1-.2 1.1.4 2.3.6 3.6.6.6 0 1 .4 1 1V20c0 .6-.4 1-1 1C10.6 21 3 13.4 3 4c0-.6.4-1 1-1h3.5c.6 0 1 .4 1 1 0 1.3.2 2.5.6 3.6.1.3 0 .7-.2 1L6.6 10.8z"/>
    </svg>
    <span>617.555.0142</span>
  </div>

  <h1 class="hero-title">Your Smile.<br>Our Passion.</h1>
</div>
</body>
</html>
```